Social responsible Renewable Energy company

We at brivoX are an independent power producer company founded in 2021 that handles large scale deployment of Renewable Energy and carbon neutral Energy as a service model. We offer turnkey solutions using solar panel systems and this could be incorporated in our business cards. You can also find our logo in the documents provided. Another key issue is that the business cards will be printed on recicled paper, not sure if this is a limitation in deciding the design. The recycled sign should also be added on the business card and stating that the paper used was recycled. Our website is www.mybrivox-example.com. It should also be very professional, not too dreamy but still needs to capture your imagination. We are really excited to get your ideas !

Target Market(s)

Renewable Energy market

Contact Information for Business Card

The business card will be printed on recycled paper. Name of the company is brivoX. Website is www.mybrivox-example.com

Requirements
Nice to have
• Our motto: Powered by renewable, driven by people.

```html
<!DOCTYPE html>
<html lang="en">
<head>
<meta charset="utf-8">
<title>brivoX business card</title>
<link href="https://fonts.googleapis.com/css2?family=Open+Sans:wght@400;600;800&display=swap" rel="stylesheet">
<style>
  :root {
    --stage: #2b2b2b;
    --card: #161616;
    --accent: #2f7fd0;
    --ink: #f2f2f2;
    --muted: #9a9a9a;
    --logo-back: #8c8c8c;
  }
  * { margin: 0; padding: 0; box-sizing: border-box; }
  html, body { width: 1200px; height: 900px; overflow: hidden; }
  body {
    background: var(--stage);
    font-family: "Open Sans", Arial, sans-serif;
    position: relative;
  }
  .card {
    position: absolute;
    left: 250px;
    width: 700px;
    height: 400px;
    background: var(--card);
    border-bottom: 6px solid var(--accent);
    box-shadow: 0 12px 30px rgba(0,0,0,.45);
  }
  .card--front { top: 40px; }
  .card--back  { top: 470px; }

  .brand-name {
    font-weight: 800;
    letter-spacing: -1px;
    line-height: 1;
  }
  .card--front .brand-name {
    position: absolute;
    left: 60px;
    top: 150px;
    font-size: 74px;
    color: var(--accent);
  }
  .divider {
    position: absolute;
    left: 345px;
    top: 70px;
    width: 2px;
    height: 260px;
    background: var(--accent);
  }
  .contact {
    position: absolute;
    left: 375px;
    top: 78px;
    color: var(--ink);
    font-size: 17px;
    line-height: 1.4;
  }
  .contact__name {
    color: var(--accent);
    font-weight: 800;
    font-size: 23px;
    letter-spacing: .5px;
    text-transform: uppercase;
  }
  .contact__title { margin-bottom: 14px; }
  .contact__address { margin-bottom: 16px; }
  .contact__line { display: flex; align-items: center; gap: 8px; }
  .contact__line svg { width: 14px; height: 14px; flex: none; }

  .back-brand {
    position: absolute;
    left: 0; right: 0;
    top: 110px;
    display: flex;
    justify-content: center;
    align-items: center;
    gap: 18px;
  }
  .back-brand .brand-name {
    font-size: 120px;
    color: var(--logo-back);
  }
  .sun-dot {
    width: 34px;
    height: 34px;
    border-radius: 50%;
    background: var(--accent);
    margin-top: 40px;
  }
  .motto {
    position: absolute;
    left: 0; right: 0;
    top: 262px;
    text-align: center;
    color: var(--accent);
    font-size: 18px;
    font-weight: 600;
    letter-spacing: .5px;
  }
  .recycled-note {
    position: absolute;
    left: 0; right: 0;
    bottom: 30px;
    display: flex;
    justify-content: center;
    align-items: center;
    gap: 10px;
    color: var(--muted);
    font-size: 14px;
  }
  .recycled-note svg { width: 26px; height: 26px; flex: none; }
</style>
</head>
<body>
  <section class="card card--front" aria-label="Business card front">
    <div class="brand-name">brivoX</div>
    <div class="divider"></div>
    <div class="contact">
      <div class="contact__name">Daniel Carver</div>
      <div class="contact__title">President</div>
      <div class="contact__address">1840 Harbor View Lane<br>Larkspur Cove CA 90000</div>
      <div class="contact__line">
        <svg viewBox="0 0 16 16" aria-hidden="true"><path fill="#2f7fd0" d="M3.5 1.5l2.5 0 1 3.5-1.8 1.2a9 9 0 0 0 4.6 4.6L11 9l3.5 1v2.5c0 1-.8 1.8-1.8 1.7C6.6 13.7 2.3 9.4 1.8 3.3 1.7 2.3 2.5 1.5 3.5 1.5z"/></svg>
        <span>555-014-2280</span>
      </div>
      <div class="contact__line">
        <svg viewBox="0 0 16 16" aria-hidden="true"><rect x="1" y="3" width="14" height="10" fill="#2f7fd0"/><path d="M1 3l7 6 7-6" fill="none" stroke="#161616" stroke-width="1.4"/></svg>
        <span>dcarver@mybrivox-example.com</span>
      </div>
      <div class="contact__line">
        <svg viewBox="0 0 16 16" aria-hidden="true"><circle cx="8" cy="8" r="6.5" fill="none" stroke="#2f7fd0" stroke-width="1.6"/><ellipse cx="8" cy="8" rx="2.8" ry="6.5" fill="none" stroke="#2f7fd0" stroke-width="1.2"/><path d="M1.5 8h13" stroke="#2f7fd0" stroke-width="1.2"/></svg>
        <span>www.mybrivox-example.com</span>
      </div>
    </div>
  </section>

  <section class="card card--back" aria-label="Business card back">
    <div class="back-brand">
      <div class="brand-name">brivoX</div>
      <div class="sun-dot" aria-hidden="true"></div>
    </div>
    <div class="motto">Powered by renewable, driven by people.</div>
    <div class="recycled-note">
      <svg viewBox="0 0 24 24" role="img" aria-label="Recycled paper sign">
        <g fill="none" stroke="#2f7fd0" stroke-width="2" stroke-linecap="round">
          <path d="M6 9.5A7 7 0 0 1 15.5 5.2"/>
          <path d="M18.8 9.5A7 7 0 0 1 15.5 18.8"/>
          <path d="M11.5 19A7 7 0 0 1 5 12.8"/>
        </g>
        <g fill="#2f7fd0">
          <path d="M17.8 5.6l-3.6 2.2.4-4.2z"/>
          <path d="M13.6 20.5l.8-4.1 3 2.9z"/>
          <path d="M3.4 10.8l4 .8-3 2.9z"/>
        </g>
      </svg>
      <span>Printed on 100% recycled paper</span>
    </div>
  </section>
</body>
</html>
```